Field Basket - Store need a label design

We need a Label Design for our Cosmetic Line with Hemp Cosmetics. We do not want a hemp leaf on our design. We want our LOGO infront of the design with the name of the product (shower gel, body lotion, .....) The ingredients must be included as well as in the bottle within 12 months. The font is smaller than 3mm. Generally, the font must be at least 2mm in size. What we need: 100x140mm 200ml E 12m 4x as: Hemp - shampoo, shower gel, body lotion and hair balm 20x66 mm 50g E (2 pieces for front and back) as: face cream, hand cream 42x52mm as: lip balm (sample how it should look in the uploaded files with the name morvil) What else should be on it: WITHOUT artificial colors and fragrances WITHOUT paraffins WITHOUT silicones with pure hemp seed oil Product not tested on animals Manufacturer: MORVIL A-4812 GRUNDLACH Description: HANF-SHAMPOO 200 ml Skin-mild washing-active ingredients develop a particularly pleasant and gentle cleansing effect. High-quality hemp seed oil nourishes the hair in a natural way and makes it pleasantly soft, loose and supple. BRISK MEADOW- is suitable for all hair types, especially for damaged and dull hair. HEMP SHOWER BATH 200 ml The pleasant foam cleans mildly and gently. The excellent care effect of natural hemp seed oil makes skin and hair pleasantly soft and supple.BRISK MEADOW- is suitable for mild cleansing and care, especially of sensitive skin and damaged hair. HEMP-FOAM BATH 200 ml Skin-mild washing-active ingredients develop a particularly mild and creamy foam. The excellent care effect of natural hemp seed oil makes the skin exceptionally soft and supple.BRISK MEADOW- is suitable for mild cleansing and care, especially of sensitive, rough and chapped skin. HEMP HAIR BALM 200 ml A special combination of natural hemp seed oil and other high-quality vegetable oils cares for the hair perfectly and makes it pleasantly soft, loose, supple, naturally shiny, extremely easy to style and effectively prevents the cleavage of the tips. BRISK MEADOW HEMP HAIR BALM is suitable for all hair types, especially for damaged, damaged, brittle and dull hair, as well as split hair tips. HEMP BODY LOTION 200 ml Pure Hemp Seed Oil nourishes the skin naturally, prevents it from drying out too much and makes it particularly soft and supple.BRISK MEADOW HEMP BODY LOTION is for pleasant body care, especially after bathing, especially in dry, brittle and sensitive skin HEMP FACE CREAM 50 g The particularly high content of pure hemp seed oil nourishes the skin perfectly and makes it unusually soft and supple.BRISK MEADOW HEMP FACE CREAM is suitable for pleasant and moisturizing care of the entire face, especially for dry and brittle skin Skin. HEMP HAND CREAM 50 g The high content of pure hemp seed oil and natural beeswax protects and nourishes the skin perfectly and makes it soft and supple. BRISK MEADOW HEMP HAND CREAM is suitable for protective care especially of stressed, sensitive and brittle skin. HEMP LIP BALM 6 g Natural hemp seed oil, pure beeswax and other valuable ingredients provide long-lasting care for the lips and protect them from adverse weather conditions and dehydration.BRISK MEADOW HEMP LIP BALM is particularly suitable for the lasting care of sensitive, brittle and torn lips. HANF-SHAMPOO Ingredients (INCI): Aqua, Sodium Laureth Sulfate, TEA-Lauryl Sulfate, Disodium Laureth Sulfosuccinate, Potassium Cocoyl Hydrolized Collagen, Linoleamide-DEA, Cannabis Sativa Seed Oil, Natural Perfume, Sodium Chloride, Citric Acid, Potassium Sorbate, Panthenol , Tocopherol, chlorophyll, citral *, citronellol *, geraniol *, limonene *, linalool *. (* natural ingredients of essential oils). HEMP-DUSCHBAD Ingredients (INCI): Aqua, Sodium Laureth Sulfate, TEA-Lauryl Sulfate, Disodium Laureth Sulfosuccinate, Potassium Cocoyl Hydrolized Collagen, Cocoamphodiacetate, Linoleamide-DEA, Cocamidopropylamine Oxide, Cannabis Sativa Seed Oil, Natural Perfume, Coco-Glucoside, Glyceryl Oleate, Sodium Chloride, Citric Acid, Potassium Sorbate, Panthenol, Tocopherol, Chlorophyll, Citral *, Citronellol *, Geraniol *, Limonene *, Linalool *. (* natural ingredients of essential oils). HANF-SCHAUMBAD Ingredients (INCI): Aqua, MIPA-Pareth-25-Sulfate, Cocamidopropyl Betaine, Disodium Laureth Sulfosuccinate, Linoleamide-DEA, Cannabis Sativa Seed Oil, Coco-Glucoside, Glyceryl Oleate, Natural Perfume, Panthenol, Potassium Sorbate, Citric Acid, tocopherol, chlorophyll, citral *, citronellol *, geraniol *, limonene *, linalool *. * (* Natural constituents of essential oils). HANF-HAARBALSAM Ingredients (INCI): Aqua, Ceteareth-20, Cetearyl Alcohol, Dicocodimonium Chloride, Glycerine, Cannabis Sativa Seed Oil, Coco-Glucoside, Glyceryl Oleate, Natural Perfume, Potassium Sorbate, Panthenol, Citric Acid, Tocopherol, Chlorophyll, Citral *, Citronellol *, geraniol *, limonene *, linalool *. (* natural ingredients of essential oils). Hemp Facial Ingredients (INCI): Aqua, Cannabis Sativa Seed Oil, Cetearyl Alcohol, Cetearyl Glucoside, Sodium Cetearyl Sulfate, Hexyl Decanol, Glycerine, Natural Perfume, Benzyl Alcohol, Potassium Sorbate, Sodium Benzoate, Tocopherol, Panthenol, Citric Acid, Citral * , Citronellol *, geraniol *, limonene *, linalool *. (* natural ingredients of essential oils). HANF HAND CREAM Ingredients (INCI): Cannabis sativa Seed Oil, Cocos Nucifera Oil, Cera Alba, Tocopherol, Natural Perfume, Citral *, Citronellol *, Geraniol *, Limonene *, Linalool *. (* natural ingredients of essential oils). HEMP BODY LOTION INGREDIENTS (INCI): Aqua, Cannabis Sativa Seed Oil, Cetearyl Alcohol, Ceteareth-12, Cetearyl Glucoside, Glycerol, Hexyldecanol, Natural Perfume, Benzyl Alcohol, Potassium Sorbate, Sodium Benzoate, Tocopherol, Panthenol, Citric Acid, Geraniol , Limonene *, linalool *, citronellol *, citral *, (* natural constituents of essential oils). HEMP LIP BALM Ingredients (INCI): Cannabis sativa Seed Oil, Cocos nucifera Oil, Cera Alba, Natural Perfume, Citral *, Citronellol *, Geraniol *, Limonene *, Linalool *. (* natural ingredients of essential oils).

Colors

Designer to choose colors to be used in the design.

Requirements
Must have
• The Sentence: Natural Spirit - Feel the nature should be in front of the label as our slogan for the Cosmetic Line
Should not have
• Hemp leaf

```html
<!DOCTYPE html>
<html lang="de">
<head>
<meta charset="utf-8">
<title>Hanf-Gesichtscreme Etikett – Brisk Meadow</title>
<link rel="stylesheet" href="https://fonts.googleapis.com/css2?family=Bebas+Neue&family=Courier+Prime:wght@400;700&family=Oswald:wght@500;600&display=swap">
<style>
  :root {
    --label-red: #c9544e;
    --label-red-light: #d66a62;
    --badge-red: #8e1c25;
    --ink-white: #fbf1ee;
  }
  * { margin: 0; padding: 0; box-sizing: border-box; }
  html, body { width: 1200px; height: 364px; overflow: hidden; background: var(--label-red); }
  .label {
    position: relative;
    width: 1200px; height: 364px;
    background: var(--label-red);
    color: var(--ink-white);
    overflow: hidden;
  }
  .ornament-area {
    position: absolute; left: 455px; top: -40px;
    width: 290px; height: 230px;
    border-radius: 50%;
    background: radial-gradient(circle, rgba(230,130,120,0.45) 0%, rgba(214,106,98,0.25) 55%, rgba(201,84,78,0) 72%);
  }
  .brand {
    position: absolute; left: 28px; top: 12px; width: 250px;
    display: flex; flex-direction: column; align-items: center;
  }
  .brand-mark {
    width: 56px; height: 56px; border-radius: 50%;
    border: 4px solid var(--ink-white);
  }
  .brand-name {
    margin-top: 14px;
    font-family: "Oswald", sans-serif; font-weight: 600;
    font-size: 29px; line-height: 1; letter-spacing: 0.5px;
  }
  .product-title {
    position: absolute; left: 26px; top: 152px;
    font-family: "Bebas Neue", sans-serif;
    font-size: 92px; line-height: 1; letter-spacing: 2px;
  }
  .title-rule {
    position: absolute; left: 28px; top: 240px;
    width: 664px; height: 3px; background: var(--ink-white);
  }
  .product-claim {
    position: absolute; left: 28px; top: 254px; width: 664px;
    text-align: center;
    font-family: "Oswald", sans-serif; font-weight: 500;
    font-size: 27px; line-height: 1; letter-spacing: 9px;
  }
  .free-from {
    position: absolute; left: 702px; top: 20px;
    list-style: none;
    font-family: "Courier Prime", monospace; font-weight: 700;
    font-size: 21px; line-height: 36px;
  }
  .free-from u { text-underline-offset: 3px; }
  .animal-badge {
    position: absolute; left: 706px; top: 230px;
    width: 146px; height: 64px;
    background: var(--badge-red);
    display: flex; align-items: center; justify-content: center; text-align: center;
    font-family: "Courier Prime", monospace; font-weight: 700;
    font-size: 12.5px; line-height: 18px;
  }
  .manufacturer {
    position: absolute; left: 930px; top: 232px;
    font-family: "Courier Prime", monospace; font-weight: 700;
    font-size: 13px; line-height: 40px; letter-spacing: 1px;
  }
</style>
</head>
<body>
  <main class="label">
    <div class="ornament-area" role="img" aria-label="Faint decorative mandala ornament"></div>

    <div class="brand">
      <span class="brand-mark"></span>
      <span class="brand-name">BRISK MEADOW</span>
    </div>

    <h1 class="product-title">HANF-GESICHTSCREME</h1>
    <div class="title-rule"></div>
    <p class="product-claim">BIOLOGISCH ABBAUBAR</p>

    <ul class="free-from">
      <li><u>OHNE</u> künstliche Farb und Geruchstoffe</li>
      <li><u>OHNE</u> Paraffine</li>
      <li><u>OHNE</u> Silikone</li>
      <li>mit reinem Hanfsamenöl</li>
    </ul>

    <div class="animal-badge">PRODUKT NICHT<br>AN TIEREN GETESTET</div>

    <div class="manufacturer">
      HERSTELLER:<br>
      MORVIL A-4812 GRUNDLACH
    </div>
  </main>
</body>
</html>
```